Simple and elegant Wallsaver Packaging needed for our new product

We are looking for a packaging for our new wallsaver product, which primary purpose is to protect damages to the wall. It prevents drilling holes into the wall.

Packaging file can be found - https://filebox.example-share.net/open?id=7Qtr2LmXvPaKsWeNcDfHjUyBnRtZ

The company name is Brondafe and i have attached pictures of the product and the company logo that we would like on the packaging.

Examples of packaging we like in terms of packaging are pellamor packaging and crane & hollis packaging.

Copies of instructions to set up the product are on the 5th picture on this link - https://www.shopvendra.example/d/kpt/Tavelo-Pressure-Protect-Surface-Gates-Curtain-Tension-Mounted/Z93KQ7WM2P.
Updates

All,I have updated the brief and add more info about the packaging so please have another look.I look forward to receiving your designs and giving feedback.Thanks Added Thursday, January 12, 2017

Hi All, We still awaiting for more entries before making our final decision. Happy to assist if anyone has further queries. Thanks

One more day left so please submit your designs. I will be giving feedback shortly on the designs received so far. A few designers have asked for me to extend the competition so they have time to submit, so i may do this. Regards Elsa

Reason: Hi, I am extending the deadline so designers can incorporate the feedback i am going to give. So i can get the best possible design possible. Thanks

Target Market(s)

Homeowners

Industry/Entity Type

Home Improvement

Requirements
Must have
• Logo, Instructions to use
Nice to have
• Pictures of product

```html
<!DOCTYPE html>
<html lang="en">
<head>
<meta charset="utf-8">
<title>Brondafe Pressure Gate Wall – Packaging</title>
<link rel="stylesheet" href="https://fonts.googleapis.com/css2?family=Fira+Sans+Condensed:ital,wght@1,500&family=Open+Sans:ital,wght@0,400;0,600;1,400&display=swap">
<style>
  :root {
    --bg: #dfe5ea;
    --green: #06a13a;
    --black: #0b0b0b;
    --white: #ffffff;
    --paper: #f4f4f4;
    --yellow: #d4ad06;
    --ink: #1c1c1c;
    --grey-light: #e6e6e6;
    --grey-mid: #b9b9b9;
    --fold: #c7cdd2;
  }
  * { margin: 0; padding: 0; box-sizing: border-box; }
  html, body { width: 1200px; height: 900px; overflow: hidden; background: var(--bg); }
  body { position: relative; font-family: "Open Sans", sans-serif; color: var(--ink); }

  .dieline { position: absolute; left: 150px; top: 40px; width: 900px; height: 820px; }
  .panel { position: absolute; overflow: hidden; outline: 1px solid var(--fold); }

  .panel--top { left: 220px; top: 0; width: 460px; height: 220px; background: var(--green);
    display: flex; flex-direction: column; align-items: center; justify-content: center; }
  .panel--front { left: 220px; top: 220px; width: 460px; height: 600px; background: var(--paper); }
  .panel--side-left { left: 0; top: 220px; width: 220px; height: 600px; background: var(--paper); }
  .panel--side-right { left: 680px; top: 220px; width: 220px; height: 600px; background: var(--paper); }

  .band-green { position: absolute; left: 0; right: 0; top: 0; height: 130px; background: var(--green); }
  .band-black { position: absolute; left: 0; right: 0; top: 130px; height: 120px; background: var(--black); }

  .product-title { position: absolute; left: 30px; top: 22px; color: var(--white);
    font-family: "Fira Sans Condensed", sans-serif; font-style: italic; font-weight: 500; line-height: 0.95; }
  .product-title .line-small { display: block; font-size: 38px; }
  .product-title .line-large { display: block; font-size: 56px; }

  .brand { color: var(--white); text-align: center; font-family: "Open Sans", sans-serif; font-weight: 400; }
  .brand__name { display: block; font-size: 46px; letter-spacing: 3px; line-height: 1; text-transform: uppercase; }
  .brand__tag { display: block; font-size: 10px; letter-spacing: 3px; margin-top: 6px; text-transform: uppercase; }
  .band-black .brand { position: absolute; left: 30px; top: 28px; text-align: left; }

  .product-photo { position: absolute; left: 275px; top: 270px; width: 160px; height: 230px;
    border-radius: 80px; background: radial-gradient(circle at 40% 35%, var(--grey-light), var(--grey-mid)); }

  .copy { position: absolute; left: 30px; top: 282px; width: 225px; font-size: 10px; line-height: 1.4; }
  .copy__heading { font-size: 12px; letter-spacing: 1px; text-transform: uppercase; text-align: center; margin-bottom: 10px; }
  .copy p { margin-bottom: 10px; }
  .copy__link { overflow-wrap: anywhere; }

  .pack-tag { position: absolute; left: 30px; top: 520px; width: 230px; height: 50px; background: var(--yellow);
    display: flex; align-items: center; justify-content: center;
    font-family: "Fira Sans Condensed", sans-serif; font-style: italic; font-weight: 500; font-size: 30px; color: var(--black); }

  .side-strip { position: absolute; left: 30px; top: 280px; width: 70px; height: 290px; background: var(--yellow); }
  .side-brand { position: absolute; left: 0; right: 0; top: 38px; }
  .side-brand .brand__name { font-size: 28px; }
  .side-brand .brand__tag { font-size: 7px; letter-spacing: 2px; }

  .scene-photo { position: absolute; left: 0; right: 0; top: 250px; bottom: 0;
    background: linear-gradient(160deg, #efeae3, #c9a67a 55%, #8b6a48); }
  .side-title { position: absolute; left: 20px; top: 152px; color: var(--white);
    font-family: "Fira Sans Condensed", sans-serif; font-style: italic; font-weight: 500; font-size: 34px; line-height: 1; }
</style>
</head>
<body>
  <main class="dieline">
    <section class="panel panel--top">
      <div class="brand">
        <span class="brand__name">Brondafe</span>
        <span class="brand__tag">Homeware Accessories</span>
      </div>
    </section>

    <section class="panel panel--side-left">
      <div class="band-green">
        <div class="brand side-brand">
          <span class="brand__name">Brondafe</span>
          <span class="brand__tag">Homeware Accessories</span>
        </div>
      </div>
      <div class="band-black"></div>
      <div class="side-strip"></div>
    </section>

    <section class="panel panel--front">
      <div class="band-green">
        <h1 class="product-title">
          <span class="line-small">PRESSURE</span>
          <span class="line-large">GATE WALL</span>
        </h1>
      </div>
      <div class="band-black">
        <div class="brand">
          <span class="brand__name">Brondafe</span>
          <span class="brand__tag">Homeware Accessories</span>
        </div>
      </div>
      <div class="product-photo" role="img" aria-label="Photo of three white round wall saver pads"></div>
      <div class="copy">
        <div class="copy__heading">Brondafe</div>
        <p>The company name is Brondafe and i have attached pictures of the product and the company logo that we would like on the packaging.</p>
        <p>Examples of packaging we like in terms of packaging are pellamor packaging and crane &amp; hollis packaging.</p>
        <p>Copies of instructions to set up the product are on the 5th picture on this link - <span class="copy__link">https://www.shopvendra.example/d/kpt/Tavelo-Pressure-Protect-Surface-Gates-Curtain-Tension-Mounted/Z93KQ7WM2P.</span></p>
      </div>
      <div class="pack-tag">SAVER 2 PACK</div>
    </section>

    <section class="panel panel--side-right">
      <div class="band-green"></div>
      <div class="band-black"></div>
      <div class="side-title">PRESSURE<br>GATE WALL</div>
      <div class="scene-photo" role="img" aria-label="Photo of a wooden safety gate fitted in a bright home hallway"></div>
    </section>
  </main>
</body>
</html>
```